Parcelwise HQ letterhead and envelope

Design a formal (8.5x11) letterhead and envelope for sales outreach and legal matters. Using design input from https://www.parcelwisehq.example/ and the attached documents.

Industry/Entity Type

Software Service

Requirements
Must have
• These 4 hex colors are our official colors:
• #355c98 [blue]
• #1eb1a2 [teal]
• #fdba12 [gold]
• #f1653b [orange]
• So no other colors besides these should be used.

```html
<!DOCTYPE html>
<html lang="en">
<head>
<meta charset="utf-8">
<title>Parcelwise HQ letterhead and envelope</title>
<link rel="stylesheet" href="https://fonts.googleapis.com/css2?family=Roboto:wght@300;400;500&display=swap">
<style>
  :root {
    --brand-blue: #355c98;
    --brand-teal: #1eb1a2;
    --brand-gold: #fdba12;
    --brand-orange: #f1653b;
    --paper: #f0f0f0;
    --backdrop: #d4d4d4;
    --ink-strong: #3a3a3a;
    --ink-soft: #6e6e6e;
    --rule: #9a9a9a;
  }
  * { box-sizing: border-box; margin: 0; padding: 0; }
  html, body { width: 1200px; height: 946px; overflow: hidden; }
  body {
    background: var(--backdrop);
    font-family: "Roboto", Arial, sans-serif;
    position: relative;
  }
  .sheet {
    position: absolute;
    background: var(--paper);
    overflow: hidden;
  }

  /* Shared brand lockup */
  .brand {
    position: absolute;
    display: flex;
    align-items: center;
    color: var(--brand-blue);
    font-weight: 300;
    white-space: nowrap;
  }
  .brand-dot {
    border: 2.5px solid var(--brand-blue);
    border-radius: 50%;
    margin-right: 9px;
    flex: none;
  }
  .contact { position: absolute; line-height: 1.55; white-space: nowrap; }
  .contact-direct { color: var(--ink-strong); font-weight: 500; }
  .contact-office { color: var(--ink-soft); }
  .watermark-ring {
    position: absolute;
    border-radius: 50%;
    border: solid var(--brand-blue);
    opacity: 0.17;
  }

  /* Letterhead */
  .letterhead { left: 107px; top: 148px; width: 478px; height: 672px; }
  .letterhead .brand { left: 30px; top: 45px; font-size: 24px; }
  .letterhead .brand-dot { width: 34px; height: 34px; }
  .letterhead .contact { font-size: 8.2px; top: 47px; }
  .letterhead .contact-direct { left: 246px; }
  .letterhead .contact-divider {
    position: absolute; left: 366px; top: 47px; width: 1px; height: 30px; background: var(--rule);
  }
  .letterhead .contact-office { left: 376px; }
  .recipient {
    position: absolute; left: 43px; top: 200px;
    font-size: 8.8px; line-height: 1.45; color: var(--ink-soft);
  }
  .letter-body {
    position: absolute; left: 43px; width: 396px;
    font-size: 8.6px; line-height: 12.5px; color: var(--ink-soft);
    text-align: justify;
  }
  .letter-body.first { top: 275px; }
  .letter-body.second { top: 387px; }
  .signature-area {
    position: absolute; left: 43px; top: 460px; width: 90px; height: 58px;
    background: linear-gradient(135deg, #e4e4e4, #dadada);
    border-radius: 4px;
  }
  .signatory {
    position: absolute; left: 42px; top: 531px; font-size: 8.6px; color: var(--ink-soft);
  }
  .letterhead .watermark-ring { left: 322px; top: 516px; width: 152px; height: 152px; border-width: 6px; }

  /* Envelope back */
  .envelope-back { left: 630px; top: 314px; width: 475px; height: 237px; }
  .flap { position: absolute; left: 0; top: 0; width: 475px; height: 72px; }
  .flap-brand {
    position: absolute; left: 0; top: 24px; width: 475px; text-align: center;
    font-size: 13px; font-weight: 300; color: var(--brand-blue);
  }

  /* Envelope front */
  .envelope-front { left: 629px; top: 584px; width: 476px; height: 237px; }
  .envelope-front .brand { left: 24px; top: 30px; font-size: 19px; }
  .envelope-front .brand-dot { width: 25px; height: 25px; margin-right: 7px; border-width: 2px; }
  .envelope-front .contact { left: 26px; font-size: 7.2px; }
  .envelope-front .contact-direct { top: 83px; }
  .envelope-front .contact-office { top: 117px; }
  .envelope-front .watermark-ring { left: 353px; top: 113px; width: 124px; height: 124px; border-width: 5px; }
</style>
</head>
<body>

  <section class="sheet letterhead" aria-label="Letterhead">
    <div class="brand"><span class="brand-dot"></span>Parcelwise HQ</div>
    <div class="contact contact-direct">(555) 014-2288<br>jsmith@parcelwisehq.example<br>www.parcelwisehq.example</div>
    <div class="contact-divider"></div>
    <div class="contact contact-office">Main: (555) 019-4410<br>72 Harbor Lane<br>Fairview, MI 40000</div>

    <p class="recipient">Dear Hollis<br>Brightmark Print Corporation<br>Department Design</p>

    <p class="letter-body first">Lorem ipsum dolor sit amet, consectetuer adipiscing elit. Aenean commodo ligula eget dolor. Aenean massa. Cum sociis natoque penatibus et magnis dis parturient montes, nascetur ridiculus mus. Donec quam felis, ultricies nec, pellentesque eu, pretium quis, sem. Nulla consequat massa quis enim. Donec pede justo, fringilla vel, aliquet nec, vulputate eget, arcu. In enim justo, rhoncus ut, imperdiet a, venenatis vitae, justo. Nullam dictum felis eu pede mollis pretium. Integer tincidunt. Cras dapibus. Vivamus elementum semper nisi.Nullam dictum felis eu pede mollis pretium. Integer tincidunt. Cras dapibus. Vivamus elementum semper nisi.felis eu pede mollis pretium. Integer tincidunt. Cras dapibus.</p>

    <p class="letter-body second">Quisque rutrum. Aenean imperdiet. Etiam ultricies nisi vel augue. Curabitur ullamcorper ultricies nisi. Nam eget dui. Etiam rhoncus. Maecenas tempus, tellus eget condimentum rhoncus, sem quam semper libero, sit amet adipiscing sem neque sed ipsum.felis pede mollis pretium. I am tincidunt. Cras dapibus.</p>

    <div class="signature-area" role="img" aria-label="Handwritten signature of the director"></div>
    <p class="signatory">Director/Excecutive Director</p>

    <div class="watermark-ring" aria-hidden="true"></div>
  </section>

  <section class="sheet envelope-back" aria-label="Envelope back">
    <svg class="flap" viewBox="0 0 475 72" role="img" aria-label="Envelope flap with a scattered pattern of small icons in brand colours">
      <defs>
        <linearGradient id="flapTone" x1="0" y1="0" x2="1" y2="0">
          <stop offset="0" stop-color="#1eb1a2" stop-opacity="0.12"/>
          <stop offset="0.5" stop-color="#f1653b" stop-opacity="0.10"/>
          <stop offset="1" stop-color="#fdba12" stop-opacity="0.12"/>
        </linearGradient>
      </defs>
      <path d="M0 0 H475 L466 60 Q464 70 452 70 H23 Q11 70 9 60 Z" fill="#ececec"/>
      <path d="M0 0 H475 L466 60 Q464 70 452 70 H23 Q11 70 9 60 Z" fill="url(#flapTone)"/>
      <path d="M9 60 Q11 70 23 70 H452 Q464 70 466 60" fill="none" stroke="#cfcfcf" stroke-width="1"/>
    </svg>
    <div class="flap-brand">Parcelwise HQ</div>
  </section>

  <section class="sheet envelope-front" aria-label="Envelope front">
    <div class="brand"><span class="brand-dot"></span>Parcelwise HQ</div>
    <div class="contact contact-direct">(555) 014-2288<br>jsmith@parcelwisehq.example<br>parcelwisehq.example</div>
    <div class="contact contact-office">Main: (555) 019-4410<br>72 Harbor Lane<br>Fairview, MI 40000</div>
    <div class="watermark-ring" aria-hidden="true"></div>
  </section>

</body>
</html>
```